Emerging Australian photographer

I'm based in Cunderdin, a small rural town in the Wheatbelt area of Western Australia. So its a good thing that I love to travel further afield both for pleasure and for work. To me that is one and the same thing in any event!

My desire is to take photos that make the viewers heart skip. I love taking photos of people doing the things they love or being with the people they love. For me, the joy of photography comes with capturing the 'moments between the moments'. I like candid photography best of all - like when the new husband is staring joyfully at his bride and at that minute is unaware of the photographer capturing the moment.

I am available for weddings, engagements, birthdays, special events, newborns, family or individual portraits. By the end of the year I will be accredited with the Southern Guild of Accredited Image Makers.

I need a card that stands out but is elegant and would sit well on the table at a wedding or be given out in the church grounds. Classy and a little bit sassy.

Target Market(s)

Consumers who are seeking photographic services, eg wedding guests who see me at work and make enquiries.

Industry/Entity Type

Church

Contact Information for Business Card

Tamsin Everly Photography
Tamsin Everly
0452 306 718
www.tamsineverly-studio.com.au
photos@tamsineverly-studio.com.au

Requirements
Must have
• Must fit with the theme in the watermarks, but be crisp and modern.
Nice to have
• However it's not essential to have the pink! Chatterly and Pipsqueak logos.
Should not have
• Old style fonts like times new roman.

```html
<!DOCTYPE html>
<html lang="en">
<head>
<meta charset="utf-8">
<title>Tamsin Everly Photography – Business Card</title>
<link href="https://fonts.googleapis.com/css2?family=Advent+Pro:wght@300&family=Comfortaa:wght@300;400&display=swap" rel="stylesheet">
<style>
  :root {
    --backdrop: #ece9e6;
    --card-black: #000000;
    --card-white: #ffffff;
    --blush: #e8a9c3;
    --ink: #333333;
    --ink-soft: #555555;
    --ornament-light: #e4e4e4;
    --ornament-mid: #9a9a9a;
  }
  * { margin: 0; padding: 0; box-sizing: border-box; }
  html, body {
    width: 1200px; height: 927px; overflow: hidden;
    background: var(--backdrop);
    font-family: "Comfortaa", sans-serif;
  }
  .canvas { position: relative; width: 1200px; height: 927px; }

  .card {
    position: absolute;
    width: 530px; height: 330px;
    overflow: hidden;
    box-shadow: 0 6px 18px rgba(0,0,0,0.25);
  }

  /* Front face */
  .card--front { left: 70px; top: 130px; background: var(--card-black); }
  .front__header {
    position: absolute; left: 0; top: 0;
    width: 100%; height: 113px;
    background: var(--card-white);
    border-bottom: 3px solid var(--blush);
  }
  .front__name {
    position: absolute; left: 20px; top: 24px;
    font-family: "Advent Pro", sans-serif;
    font-weight: 300; font-size: 36px; color: var(--ink);
    letter-spacing: 0;
  }
  .front__tagline {
    position: absolute; left: 20px; top: 74px;
    display: flex; align-items: center; gap: 8px;
    font-weight: 300; font-size: 16px; color: var(--ink-soft);
  }
  .front__tagline svg { width: 18px; height: 16px; }
  .front__badge {
    position: absolute; right: 28px; top: 0;
    width: 118px; height: 116px;
    border-radius: 0 0 59px 59px;
    border: 1.5px solid var(--card-black);
    border-top: none;
    background: var(--card-white);
  }
  .front__ornament {
    position: absolute; right: 18px; top: 116px;
    width: 108px; height: 214px;
  }
  .front__contact {
    position: absolute; left: 24px; bottom: 14px;
    color: var(--card-white); font-weight: 300;
  }
  .front__phone { font-size: 20px; margin-bottom: 4px; }
  .front__line { font-size: 14px; line-height: 1.3; }

  /* Back face */
  .card--back { left: 600px; top: 470px; background: var(--card-black); }
  .back__brand {
    position: absolute; left: 0; top: 112px; width: 100%;
    display: flex; justify-content: center; align-items: center; gap: 14px;
  }
  .back__brand-mark {
    width: 22px; height: 22px; border-radius: 50%;
    border: 2px solid var(--card-white);
  }
  .back__brand-name {
    font-weight: 300; font-size: 30px; color: var(--blush);
    letter-spacing: 0.5px;
  }
  .back__tagline {
    position: absolute; left: 0; top: 160px; width: 100%;
    text-align: center;
    font-weight: 300; font-size: 13px; letter-spacing: 3px;
    color: var(--card-white); text-transform: lowercase;
  }
  .back__border {
    position: absolute; left: 0; bottom: 0;
    width: 530px; height: 138px; display: block;
  }
</style>
</head>
<body>
<main class="canvas">

  <section class="card card--front" aria-label="Card front">
    <header class="front__header">
      <h1 class="front__name">Tamsin Everly</h1>
      <p class="front__tagline">
        <svg viewBox="0 0 20 18" aria-hidden="true"><path d="M10 16 C4 11 1 8 1 5 A4 4 0 0 1 10 4 A4 4 0 0 1 19 5 C19 8 16 11 10 16 Z" fill="none" stroke="var(--blush)" stroke-width="1.6"/></svg>
        photos that make your heart skip
      </p>
      <div class="front__badge" role="img" aria-label="Accreditation badge"></div>
    </header>
    <svg class="front__ornament" viewBox="0 0 108 214" role="img" aria-label="Vertical swirling floral ornament with small hearts">
      <defs>
        <linearGradient id="frontOrnamentTone" x1="0" y1="0" x2="0" y2="1">
          <stop offset="0" stop-color="var(--card-white)"/>
          <stop offset="0.65" stop-color="var(--ornament-light)"/>
          <stop offset="1" stop-color="var(--ornament-mid)"/>
        </linearGradient>
      </defs>
      <path d="M40 0 Q14 27 40 54 T40 108 T40 162 T40 214 L108 214 L108 0 Z" fill="url(#frontOrnamentTone)"/>
    </svg>
    <div class="front__contact">
      <p class="front__phone">0452 306 718</p>
      <p class="front__line">www.tamsineverly-studio.com.au</p>
      <p class="front__line">photos@tamsineverly-studio.com.au</p>
    </div>
  </section>

  <section class="card card--back" aria-label="Card back">
    <div class="back__brand">
      <span class="back__brand-mark" aria-hidden="true"></span>
      <span class="back__brand-name">Tamsin Everly Photography</span>
    </div>
    <svg class="back__border" viewBox="0 0 530 138" role="img" aria-label="Border of swirling floral ornaments with small pink hearts">
      <defs>
        <linearGradient id="backBorderTone" x1="0" y1="0" x2="0" y2="1">
          <stop offset="0" stop-color="var(--ornament-light)"/>
          <stop offset="0.7" stop-color="var(--card-white)"/>
        </linearGradient>
      </defs>
      <path d="M0 44 Q27 14 53 44 T106 44 T159 44 T212 44 T265 44 T318 44 T371 44 T424 44 T477 44 T530 44 L530 138 L0 138 Z" fill="url(#backBorderTone)"/>
      <rect x="0" y="116" width="530" height="22" fill="var(--card-white)"/>
    </svg>
  </section>

</main>
</body>
</html>
```